TRELOS - Web Design Project

Task Description
RELOS is the major GLOVRA project supporting the Indonesian Bureau of Tidal Works and Harvests (BTWH). BTWH is responsible for promoting sustainable use of fish and other marine resources for Indonesia’s long-term economic prosperity. Its mandate encompasses such issues as drafting of marine and fisheries sector policies; control of overfishing, destructive and illegal fishing practices; spatial planning for resource use; management of conservation areas; data analysis and modeling for fisheries management; and promoting the long-term welfare of fishing communities. The TRELOS project is supporting BTWH efforts to achieve sustainability in the marine and fisheries sector and to improve the response of coastal communities to near-term disasters and long-term impacts related to climate change.

The TRELOS project has three key thematic areas: [policy] [1], [sustainable fisheries] [2], and [climate change] [3] — as well as supporting overall coordination of [Coastal Stewardship Scheme] [4] activities.
Updates

Project Deadline Extended
Reason: There are two public holidays in Indonesia so we are unable to provide feedback to designers between 17th and the 20th.

a few people have asked for reference sites - there is really no reference site we can give but I have attached a jpg for some ideas - we are after innovated ideas that will capture people's attention but which is extermely easy to use and navigate. 

the main focus should be on a map on Indonesia with focal points of our three offices (and with great navigation buttons/tools). 

please give us something amazing and use your design skills to make an amazing site

thanks

Target Market(s)

under 25, college or uni - research students - others interested in marine and fisheries

Industry/Entity Type

Sustainability

Requirements
Must have
• The web must have Indonesia map on the center with button on Jakarta city as headquarter, Sulawesi Tenggara (Wakatobi) as branch office and Nusa Tenggara Barat (Mataram), must have an icon for navigation on the upper, left or bottom side. Example of layout is attached (only as example). The "buttons" should then be used as navigation tools

We are after innovative ideas that with easy navigation features.

Current website is www.trelosworks.com - this is seen as too hard to navigate

Navigation Icons will also need to be developed;
- About
- Activities
- News
Library
Press releases
Publications
- Partners
- Links

site will also need to adhere to these the GLOVRA branding guidelines
http://www.glovra.example/identity/GLOVRA_Visual_Rules_Guide.pdf

TRELOS Logo is attached

Nice to have
• - based on scaffold plinko, site will be hosted on stavelo9 platform. (http://plinko.codebarn.example/)

```html
<!DOCTYPE html>
<html lang="en">
<head>
<meta charset="utf-8">
<title>TRELOS Project – Publications</title>
<link rel="stylesheet" href="https://fonts.googleapis.com/css2?family=Open+Sans:ital,wght@0,300;0,400;0,700;1,400&display=swap">
<style>
  :root {
    --page-bg: #f5f5f5;
    --brand-blue: #0d4a96;
    --link-blue: #2f6db5;
    --text: #333333;
    --muted: #8a8a8a;
    --line: #dddddd;
    --hero-light: #72b2e2;
    --hero-dark: #3f69b6;
    --icon: #555555;
  }
  * { box-sizing: border-box; margin: 0; padding: 0; }
  html, body { width: 1200px; height: 1051px; overflow: hidden; }
  body {
    position: relative;
    background: var(--page-bg);
    font-family: "Open Sans", sans-serif;
    color: var(--text);
  }

  /* Header */
  .brand { position: absolute; left: 128px; top: 25px; display: flex; align-items: center; gap: 10px; }
  .brand-dot { width: 66px; height: 66px; border-radius: 50%; border: 2px solid var(--brand-blue); }
  .brand-name { font-size: 44px; font-weight: 700; color: var(--brand-blue); letter-spacing: -0.5px; line-height: 1; }
  .project-band {
    position: absolute; left: 128px; top: 109px; width: 541px; height: 27px;
    background: var(--brand-blue); color: #fff; font-size: 13.5px; font-weight: 700;
    display: flex; align-items: center; justify-content: center; white-space: nowrap;
  }

  .language {
    position: absolute; left: 858px; top: 0; width: 232px; height: 33px;
    background: #fff; border-radius: 0 0 8px 8px; box-shadow: 0 1px 3px rgba(0,0,0,.18);
    display: flex; align-items: center; padding-left: 15px; font-size: 12px;
  }
  .language-label { color: var(--muted); margin-left: 8px; margin-right: 28px; }
  .language a { color: var(--link-blue); text-decoration: none; }
  .language .sep { color: var(--link-blue); margin: 0 6px; }

  /* Navigation */
  .main-nav {
    position: absolute; left: 110px; top: 172px; width: 980px; height: 44px;
    background: linear-gradient(#ffffff, #f0f0f0); border-radius: 8px;
    box-shadow: 0 1px 4px rgba(0,0,0,.25);
  }
  .nav-item { position: absolute; top: 0; height: 43px; display: flex; align-items: center; gap: 9px; font-size: 15px; color: var(--text); }
  .nav-item svg { fill: var(--icon); }
  .search {
    position: absolute; left: 728px; top: 7px; width: 246px; height: 31px;
    background: #fff; border-radius: 6px; box-shadow: inset 0 0 0 1px #e6e6e6;
    display: flex; align-items: center; padding-left: 16px;
    font-size: 13px; font-style: italic; color: #a5a5a5;
  }
  .search svg { position: absolute; right: 10px; top: 6px; }

  /* Content panel */
  .panel {
    position: absolute; left: 110px; top: 242px; width: 980px; height: 820px;
    background: #fff; border: 1px solid var(--line); border-radius: 8px 8px 0 0; overflow: hidden;
  }
  .page-hero {
    height: 121px; background: linear-gradient(100deg, var(--hero-light), var(--hero-dark));
    position: relative;
  }
  .hero-icon {
    position: absolute; left: 0; top: 0; width: 117px; height: 121px;
    background: linear-gradient(160deg, #5d9fd8, #3a63b2);
    display: flex; align-items: center; justify-content: center;
  }
  .page-title { position: absolute; left: 141px; top: 26px; font-size: 48px; font-weight: 300; color: #fff; }

  .publication { padding: 34px 22px 0 22px; height: 331px; white-space: nowrap; }
  .publication + .publication { border-top: 1px solid var(--line); padding-top: 31px; }
  .publication h2 { font-size: 21px; font-weight: 400; margin-bottom: 8px; }
  .publication p { font-size: 13.4px; line-height: 18px; margin-bottom: 18px; }
</style>
</head>
<body>

<header>
  <div class="brand">
    <span class="brand-dot"></span>
    <span class="brand-name">GLOVRA | INDONESIA</span>
  </div>
  <div class="project-band">COASTAL TIDES AND CLIMATE RESILIENCE (TRELOS) PROJECT</div>

  <div class="language">
    <svg width="18" height="18" viewBox="0 0 18 18"><circle cx="9" cy="9" r="8" fill="#9a9a9a"/><path d="M4 5c2 0 3 1 3 3s2 2 1 4-2 2-2 4M12 3c-1 2 1 3 3 3" stroke="#fff" stroke-width="1.4" fill="none"/></svg>
    <span class="language-label">language</span>
    <a href="#">English</a><span class="sep">|</span><a href="#">Bahasa</a>
  </div>
</header>

<nav class="main-nav">
  <div class="nav-item" style="left:16px">
    <svg width="20" height="18" viewBox="0 0 20 18"><path d="M10 1 1 9h3v8h4v-5h4v5h4V9h3z"/></svg>
  </div>
  <div class="nav-item" style="left:73px">
    <svg width="26" height="14" viewBox="0 0 26 14"><path d="M1 2c3 0 5 3 7 5-2 2-4 5-7 5l2-5zM8 7c3-5 10-6 17 0-7 6-14 5-17 0z" fill="none" stroke="#555" stroke-width="2"/></svg>About
  </div>
  <div class="nav-item" style="left:203px">
    <svg width="20" height="20" viewBox="0 0 20 20"><circle cx="12" cy="3" r="2.5"/><path d="M9 6h5l2 4h3v2h-4l-1-2-2 3 3 3v4h-2v-3l-3-2-2 3H3v-2h3l3-6-2 1-1 3H4l1-4z"/></svg>Activities
  </div>
  <div class="nav-item" style="left:352px">
    <svg width="22" height="22" viewBox="0 0 22 22"><circle cx="11" cy="11" r="9.5" fill="none" stroke="#555" stroke-width="2"/><path d="M6 4c2 2 4 1 4 4s-3 2-3 5 2 3 1 6M14 3c0 3 2 3 5 4M15 12c2 1 2 4 0 6"/></svg>News
  </div>
  <div class="nav-item" style="left:480px">
    <svg width="24" height="18" viewBox="0 0 24 18"><path d="M1 6 6 2l4 2 3-2 6 2 4 3-3 1-7-4-3 3 5 4-3 4-4-4-4-1z"/></svg>Partners
  </div>
  <div class="nav-item" style="left:627px">
    <svg width="22" height="20" viewBox="0 0 22 20" fill="none" stroke="#555" stroke-width="2.2"><rect x="2" y="3" width="10" height="6" rx="3" transform="rotate(35 7 6)"/><rect x="10" y="11" width="10" height="6" rx="3" transform="rotate(35 15 14)"/></svg>Links
  </div>
  <div class="search">Search on this site
    <svg width="20" height="20" viewBox="0 0 20 20" fill="none" stroke="#3a6cb5" stroke-width="2.2"><circle cx="12" cy="8" r="5.5"/><path d="M8 12 2 18"/></svg>
  </div>
</nav>

<main class="panel">
  <div class="page-hero">
    <div class="hero-icon">
      <svg width="50" height="60" viewBox="0 0 50 60" fill="none" stroke="#fff" stroke-width="3"><path d="M2 2h32l14 14v42H2z"/><path d="M34 2v14h14M10 26h30M10 34h30M10 42h30M10 50h30"/></svg>
    </div>
    <h1 class="page-title">Publications</h1>
  </div>

  <section class="publication">
    <h2>Lorem ipsum dolor sit amet</h2>
    <p>Lorem ipsum dolor sit amet, consectetuer adipiscing elit, sed diam nonummy nibh euismod tincidunt ut laoreet dolore magna aliquam erat volutpat.<br>Ut wisi enim ad minim veniam.</p>
    <p>quis nostrud exerci tation ullamcorper suscipit lobortis nisl ut aliquip ex ea commodo consequat. Duis autem vel eum iriure dolor in hendrerit in<br>vulputate velit esse molestie consequat, vel illum dolore eu feugiat nulla facilisis at vero eros et accumsan et iusto odio dignissim qui blandit praesent<br>luptatum zzril delenit augue duis dolore te feugait nulla facilisi. xerci tation ullamcorper suscipit lobortis nisl ut aliquip ex ea commodo consequat.<br>Duis autem vel eum iriure dolor in hendrerit in</p>
    <p>vulputate velit esse molestie consequat, vel illum dolore eu feugiat nulla facilisis at vero eros et accumsan et iusto odio dignissim qui blandit praesent<br>&nbsp;augue duis dolore te feugait nulla facilisi. xerci tation ullamcorper suscipit lobortis nisl ut aliquip ex ea commodo consequat.<br>vel eum iriure dolor in hendrerit in vulputate velit esse molestie consequat, vel illum dolore eu feugiat nulla facilisis at vero eros et accumsan et iusto<br>odio dignissim qui blandit praesent luptatum zzril delenit augue duis dolore te feugait nulla facilisi.</p>
  </section>

  <section class="publication">
    <h2>Lorem ipsum dolor sit amet</h2>
    <p>Lorem ipsum dolor sit amet, consectetuer adipiscing elit, sed diam nonummy nibh euismod tincidunt ut laoreet dolore magna aliquam erat volutpat.<br>Ut wisi enim ad minim veniam.</p>
    <p>quis nostrud exerci tation ullamcorper suscipit lobortis nisl ut aliquip ex ea commodo consequat. Duis autem vel eum iriure dolor in hendrerit in<br>vulputate velit esse molestie consequat, vel illum dolore eu feugiat nulla facilisis at vero eros et accumsan et iusto odio dignissim qui blandit praesent<br>luptatum zzril delenit augue duis dolore te feugait nulla facilisi. xerci tation ullamcorper suscipit lobortis nisl ut aliquip ex ea commodo consequat.<br>Duis autem vel eum iriure dolor in hendrerit in</p>
    <p>vulputate velit esse molestie consequat, vel illum dolore eu feugiat nulla facilisis at vero eros et accumsan et iusto odio dignissim qui blandit praesent<br>&nbsp;augue duis dolore te feugait nulla facilisi. xerci tation ullamcorper suscipit lobortis nisl ut aliquip ex ea commodo consequat.<br>vel eum iriure dolor in hendrerit in vulputate velit esse molestie consequat, vel illum dolore eu feugiat nulla facilisis at vero eros et accumsan et iusto<br>odio dignissim qui blandit praesent luptatum zzril delenit augue duis dolore te feugait nulla facilisi.</p>
  </section>
</main>

</body>
</html>
```